Professional & attention grabbing.

A business card design, front and back. I already have a logo I will attach, but I am open to something new as well.
Things to include:
Name:
Title:
Phone:
Email:
Wanting something that is professional but attention grabbing.
Also we do a lot of work using drones on natural gas pipelines (leading the future)if you want to include any of that. I'm open to ideas.
Target Market(s)
Natural gas transmission industry / greenhouse gas mitigation industry
Industry/Entity Type
Business
Colors
Designer to choose colors to be used in the design.
Look and feel
Each slider illustrates characteristics of the customer's brand and the style your logo design should communicate.

```html
<!DOCTYPE html>
<html lang="en">
<head>
<meta charset="utf-8">
<title>Ridgeway Inspections – Business Cards</title>
<link rel="stylesheet" href="https://fonts.googleapis.com/css2?family=Arimo:wght@400;700&display=swap">
<style>
  :root {
    --red: #c41e24;
    --red-dark: #8e1217;
    --black: #0d0d0d;
    --ink: #2e2e30;
    --white: #ffffff;
    --ground: #d9d9d9;
    --font: "Arimo", Arial, sans-serif;
  }
  html, body {
    margin: 0;
    padding: 0;
    width: 1200px;
    height: 732px;
    overflow: hidden;
    background: var(--ground);
    font-family: var(--font);
  }
  .sheet {
    position: relative;
    width: 1200px;
    height: 732px;
  }
  .card {
    position: absolute;
    top: 211px;
    width: 540px;
    height: 309px;
    background: var(--white);
    overflow: hidden;
    box-shadow: 0 4px 14px rgba(0,0,0,0.18);
  }
  .card--front { left: 40px; }
  .card--back  { left: 620px; }

  /* shared logo tile */
  .logo-tile {
    position: absolute;
    background: var(--white);
    border-radius: 28px;
    display: flex;
    align-items: center;
    justify-content: center;
    gap: 10px;
  }
  .wordmark {
    font-family: var(--font);
    font-weight: 700;
    color: var(--ink);
    letter-spacing: 0.5px;
  }
  .wordmark-square {
    width: 18px;
    height: 18px;
    background: var(--red);
  }
  .tab {
    position: absolute;
    background: var(--red);
  }

  /* front */
  .front-band {
    position: absolute;
    left: 0;
    top: 228px;
    width: 540px;
    height: 81px;
    background: var(--red);
  }
  .front-band__name {
    position: absolute;
    left: 34px;
    top: 22px;
    color: var(--white);
    font-size: 25px;
    letter-spacing: 0.5px;
  }
  .card--front .logo-tile {
    left: 195px;
    top: 50px;
    width: 200px;
    height: 180px;
    box-shadow: 0 0 18px rgba(196,30,36,0.45);
  }
  .card--front .wordmark { font-size: 24px; }
  .card--front .tab--top { left: 180px; top: 36px; width: 34px; height: 20px; }
  .card--front .tab--bottom { left: 376px; top: 214px; width: 34px; height: 22px; }

  /* back */
  .back-panel {
    position: absolute;
    left: 0;
    top: 0;
    width: 232px;
    height: 309px;
    background: var(--black);
  }
  .card--back .logo-tile {
    left: 32px;
    top: 34px;
    width: 186px;
    height: 176px;
  }
  .card--back .wordmark { font-size: 22px; }
  .card--back .tab--top { left: 232px; top: 0; width: 48px; height: 18px; }
  .card--back .tab--bottom { left: 200px; top: 290px; width: 48px; height: 19px; }
  .back-rail {
    position: absolute;
    right: 0;
    top: 0;
    width: 46px;
    height: 309px;
    background: var(--red);
  }
  .back-banner {
    position: absolute;
    left: 232px;
    top: 96px;
    width: 262px;
    height: 36px;
    background: var(--red);
    color: var(--white);
    font-size: 15px;
    line-height: 36px;
    padding-left: 14px;
    box-sizing: border-box;
    letter-spacing: 0.3px;
  }
  .contact-list {
    position: absolute;
    left: 248px;
    top: 146px;
    margin: 0;
    padding: 0;
    list-style: none;
  }
  .contact-list li {
    display: flex;
    align-items: center;
    gap: 10px;
    margin-bottom: 12px;
    color: var(--red);
    font-size: 12px;
    font-weight: 700;
    line-height: 1.15;
  }
  .contact-icon {
    flex: none;
    width: 22px;
    height: 22px;
  }
</style>
</head>
<body>
<main class="sheet">

  <section class="card card--front" aria-label="Card front">
    <div class="tab tab--top"></div>
    <div class="logo-tile">
      <span class="wordmark-square"></span>
      <span class="wordmark">RIDGEWAY</span>
    </div>
    <div class="tab tab--bottom"></div>
    <div class="front-band">
      <span class="front-band__name">RIDGEWAY INSPECTIONS</span>
    </div>
  </section>

  <section class="card card--back" aria-label="Card back">
    <div class="back-panel"></div>
    <div class="logo-tile">
      <span class="wordmark-square"></span>
      <span class="wordmark">RIDGEWAY</span>
    </div>
    <div class="tab tab--top"></div>
    <div class="tab tab--bottom"></div>
    <div class="back-rail"></div>
    <div class="back-banner">RIDGEWAY INSPECTIONS</div>
    <ul class="contact-list">
      <li>
        <svg class="contact-icon" viewBox="0 0 22 22" aria-hidden="true">
          <circle cx="11" cy="11" r="11" fill="#c41e24"/>
          <path d="M11 5a4 4 0 0 0-4 4c0 3 4 8 4 8s4-5 4-8a4 4 0 0 0-4-4z" fill="#fff"/>
          <circle cx="11" cy="9" r="1.5" fill="#c41e24"/>
        </svg>
        <span>Natural gas<br>transmission industry</span>
      </li>
      <li>
        <svg class="contact-icon" viewBox="0 0 22 22" aria-hidden="true">
          <circle cx="11" cy="11" r="11" fill="#c41e24"/>
          <path d="M8 5.5l2 3-1.3 1.2c.7 1.5 1.9 2.7 3.4 3.4L13.3 12l3 2-1 2.2c-4.6-.3-8.2-3.9-8.5-8.5z" fill="#fff"/>
        </svg>
        <span>55501 42187</span>
      </li>
      <li>
        <svg class="contact-icon" viewBox="0 0 22 22" aria-hidden="true">
          <circle cx="11" cy="11" r="11" fill="#c41e24"/>
          <rect x="5.5" y="7" width="11" height="8" fill="#fff"/>
          <path d="M5.5 7l5.5 4.5L16.5 7" fill="none" stroke="#c41e24" stroke-width="1.2"/>
        </svg>
        <span>HELLO@RIDGEWAY.COM</span>
      </li>
    </ul>
  </section>

</main>
</body>
</html>
```